Etikett für Rotweinflasche
Liebe farbkosmos Atelier, wir werden uns bei der endgültigen Etikettengestaltung (finale Größe + Rückseite) noch an Euch melden. Bitte sendet uns euren Kontakt an helga.brandt@morvelli.wine
Zielgruppe
Morvelli Italia ist ein exklusives Boutique-Weingut in Sizilien, das hochqualitative Spitzenweine in kleinen Mengen mit modernster Technologie und stets nachhaltig erzeugt. Wir hinterfragen sowohl in der Agronomie im Weingarten als auch in der Önologie im Weinkeller alle herrschenden Traditionen und trachten danach, stets das beste Endprodukt zu kreieren. Der vulkanische, kalkreiche Boden Siziliens sowie trockene, sonnenreiche und niederschlagsarme Vegetationsperioden sind unsere optimale Basis.
Zielgruppe: Internationale Genussmenschen jeglichen Alters, die sich bewusst auch höherpreisige Weine (um die €30+) gönnen , vor allem kunstaffine young professionals mit Qualitäts-& Nachhaltigkeitsanspruch
Aufgabenstellung
Das Etikett ist für Rotwein-Flaschen (Cabernet Sauvignon / Nero D'Avola / Frappato / Syrah / Cerasuolo / Petit Verdot / sowie einen Bourdeaux-Cuveè aus Cabernet Sauvignon und Petit Verdot) .
Die Flasche ist reinschwarz, sehr hochwertig und schwer.
Flaschenform: Bordeauxflasche siehe technisches Datenblatt
Sleeve über dem Korken: schwarz mit weißer Schrift wie bisher
Zu gestalten ist das Etikett der Vorderseite. Zumindest die jeweilige Rotwein-Sorte ist auch textlich darzustellen (zwecks Scannen mit Trubel-App)
Der Kreativität kann freien Lauf gelassen werden! Unterscheidbarkeit vom Markt ist explizit gewollt.
Unsere aktuellen Etiketten und Markenauftritt siehe: https://morvelli.wine/shop/

```html
<!DOCTYPE html>
<html lang="de">
<head>
<meta charset="utf-8">
<title>Syrah – Etikett Vorderseite</title>
<link rel="stylesheet" href="https://fonts.googleapis.com/css2?family=Cormorant+Garamond:wght@400;500&display=swap">
<style>
  :root {
    --stage: #000000;
    --label: #0b0b0c;
    --label-edge: #161617;
    --type: #c9c9cc;
    --figure-dark: #141316;
    --figure-mid: #2a2530;
    --wine-red: #a3203c;
    --wine-deep: #4a0f1c;
  }
  * { margin: 0; padding: 0; box-sizing: border-box; }
  html, body {
    width: 1200px;
    height: 1187px;
    overflow: hidden;
    background: var(--stage);
  }
  .canvas {
    position: relative;
    width: 1200px;
    height: 1187px;
    background: var(--stage);
  }
  .front-label {
    position: absolute;
    left: 250px;
    top: 91px;
    width: 700px;
    height: 1004px;
    background: var(--label);
    box-shadow: inset 0 0 0 1px var(--label-edge);
    overflow: hidden;
  }
  .varietal {
    position: absolute;
    top: 82px;
    left: 0;
    width: 100%;
    text-align: center;
    font-family: "Cormorant Garamond", serif;
    font-weight: 500;
    font-size: 34px;
    letter-spacing: 0.9em;
    padding-left: 0.9em;
    color: var(--type);
  }
  .portrait-scene {
    position: absolute;
    left: 262px;
    top: 173px;
    width: 423px;
    height: 772px;
    background:
      radial-gradient(ellipse 38% 22% at 42% 62%, rgba(120, 24, 44, 0.55), transparent 70%),
      linear-gradient(180deg, var(--figure-mid) 0%, var(--figure-dark) 45%, var(--label) 100%);
  }
  .berry-orb {
    position: absolute;
    width: 80px;
    height: 80px;
    border-radius: 50%;
    background: radial-gradient(circle at 50% 52%, var(--wine-red) 0%, var(--wine-deep) 38%, #1c1a1d 62%, #262428 100%);
    box-shadow: 0 0 0 1px rgba(255,255,255,0.06);
  }
  .orb-one   { left: 70px;  top: 560px; }
  .orb-two   { left: 176px; top: 662px; }
  .orb-three { left: 313px; top: 800px; }
</style>
</head>
<body>
  <main class="canvas">
    <section class="front-label">
      <h1 class="varietal">SYRAH</h1>
      <div class="portrait-scene" role="img" aria-label="Fotografie eines Mädchens im dunklen Samtkleid mit roter Schnürung, im Profil vor schwarzem Grund"></div>
      <div class="berry-orb orb-one" role="img" aria-label="Kleine Kugel mit roter Traubenbeere"></div>
      <div class="berry-orb orb-two" role="img" aria-label="Kleine Kugel mit roter Traubenbeere"></div>
      <div class="berry-orb orb-three" role="img" aria-label="Kleine Kugel mit roter Traubenbeere"></div>
    </section>
  </main>
</body>
</html>
```